Schlichtes Design für Malerbetrieb
Zielgruppe
Wir sind ein mittelgroßer Malerbetrieb in München mit umfangreichem Leistungsspektrum.
Unsere Hauptleistungen sind: Fassadenrenovierung, Altbausanierung, Betoninstandsetzung, Balkonabdichtung (kein Neubau!).
Unsere Zielgruppen sind: Hausverwaltungen, Firmen und Privatpersonen.
Unsere Kunden schätzen: Konstruktive Organisation und Planung im Vorfeld, Zuverlässigkeit, saubere Arbeitsweise, dauerhafte Balkonabdichtungen.
Aufgabenstellung
Wir möchten eine langlebige, stilvolle, minimalistische Homepage.
Wir möchten von der bestehenden Homepage nur die Schriftart für unseren Firmennamen (Century Gothic) und wenn möglich (nicht zwingend), irgendwo das florale Muster einbauen. Corporate-Design haben wir nicht.
Farbtöne: Firmennamen Orange (hellorange bis erdiges Orange möglich, da sind wir nicht fixiert) , einen dunklen Hintergrundfarbton (Petrol-Blaugrau ?) mit gelbem (neon bis senfgelb) Akzent (Linien), Blumenmuster weiß, grau.
Dies sind nur unsere Ideen. Wir sind aber auch absolut offen für eure Profi-Ideen.
Wir möchten uns von den unzähligen langweiligen 'Pinselseiten mit veralteten Bilder' unserer Kollegen interessant und mit Stil abheben.
Eher nach dem Motto 'weniger ist mehr'.
Einen positiven, sympathischen Eindruck geben und unsere Leistungen in den Vordergrund bringen.
Da wir viele Stammkunden haben, betreiben wir kein Social-Media und möchten dies vorerst auch nicht tun.
Die Seite wird in den nächsten Jahren nicht verändert, höchstens die Bilder aktualisiert.
Die Texte haben wir alle selbst entworfen und möchten wir so übernehmen.
Die Galerien sollen unkompliziert anzuschauen sein.
Uns gefällt die Struktur und Schlichtheit von https://vaartmolen.nl/ oder Timbra.de gut und wir mögen Vintage-Grafiken gerne.
Einerseits darf die Seite geradlinig, andererseits aber auch rund und floral wirken.

```html
<!DOCTYPE html>
<html lang="de">
<head>
<meta charset="utf-8">
<title>Kolbrit – Malerbetrieb</title>
<link rel="stylesheet" href="https://fonts.googleapis.com/css2?family=Bebas+Neue&family=Questrial&family=Sacramento&display=swap">
<style>
  :root {
    --accent: #f5b335;
    --ink: #454545;
    --paper: #ffffff;
    --paper-soft: #f4f4f4;
    --footer: #42425a;
    --sky: #b9d6ef;
    --stone-light: #c9c9c9;
    --stone-dark: #7d7d7d;
  }
  * { box-sizing: border-box; margin: 0; padding: 0; }
  html, body { width: 692px; height: 1200px; overflow: hidden; background: var(--paper); }
  body { position: relative; font-family: "Questrial", sans-serif; color: var(--ink); }

  .site-header { position: absolute; top: 0; left: 0; width: 692px; height: 66px; }
  .brand { position: absolute; left: 24px; top: 10px; font-family: "Questrial", sans-serif; font-size: 42px; line-height: 1; color: var(--accent); letter-spacing: 1px; }
  .main-nav { position: absolute; left: 236px; top: 43px; display: flex; gap: 10px; }
  .main-nav a { font-family: "Bebas Neue", sans-serif; font-size: 11px; letter-spacing: 0.4px; color: var(--ink); text-decoration: none; }

  .hero { position: absolute; top: 66px; left: 0; width: 692px; height: 325px;
    background: linear-gradient(180deg, var(--sky) 0%, #dfe9f2 45%, #e2643a 60%, #d9552d 100%); }
  .hero-caption { position: absolute; left: 412px; top: 71px; color: #fff; }
  .hero-caption h2 { font-family: "Bebas Neue", sans-serif; font-weight: 400; font-size: 20px; line-height: 1; }
  .hero-caption p { font-size: 12.5px; margin-top: 4px; }

  .intro { position: absolute; top: 420px; left: 0; width: 692px; text-align: center; }
  .intro h1 { font-family: "Bebas Neue", sans-serif; font-weight: 400; font-size: 30px; letter-spacing: 0.5px; color: var(--ink); line-height: 1; }
  .intro p { font-size: 12.5px; margin-top: 11px; }
  .intro .signature { font-family: "Sacramento", cursive; font-size: 32px; color: var(--accent); margin-top: 8px; line-height: 1; }

  .services { position: absolute; top: 560px; left: 0; width: 692px; height: 429px;
    display: grid; grid-template-columns: 172px 173px 173px 174px; grid-template-rows: 143px 143px 143px; }
  .photo { display: block; }
  .photo--square-building { grid-column: 1 / 3; grid-row: 1 / 3; background: linear-gradient(180deg, #d8d8d8 0%, #9a9a9a 55%, #c4c4c4 100%); }
  .photo--concrete { grid-column: 4; grid-row: 1; background: linear-gradient(135deg, #a8a8a8, #6e6e6e); }
  .photo--balcony { grid-column: 3; grid-row: 2; background: linear-gradient(180deg, #d9c4ab 0%, #8a6a52 35%, #e6e6e6 60%, #cfcfcf 100%); }
  .photo--doorway { grid-column: 1; grid-row: 3; background: linear-gradient(180deg, #e8e8e8 0%, #b0b0b0 50%, #4a4a4a 100%); }
  .photo--facade { grid-column: 3 / 5; grid-row: 3; background: linear-gradient(180deg, #cfe0f0 0%, #d47a5c 20%, #ece4e8 40%, #dcd6da 100%); }

  .service-card { padding: 30px 0 0 18px; background: var(--paper); }
  .service-card--soft { background: var(--paper-soft); padding-left: 27px; }
  .service-card--concrete { grid-column: 3; grid-row: 1; }
  .service-card--balcony { grid-column: 4; grid-row: 2; }
  .service-card--insulation { grid-column: 2; grid-row: 3; padding-left: 26px; }
  .service-card h3 { font-family: "Bebas Neue", sans-serif; font-weight: 400; font-size: 15px; line-height: 1; color: var(--ink); }
  .service-card p { font-size: 12.5px; margin-top: 11px; }
  .button { display: inline-block; margin-top: 11px; background: var(--accent); color: #fff; font-family: "Bebas Neue", sans-serif; font-size: 14px; line-height: 1; padding: 5px 10px 4px; text-decoration: none; }

  .site-footer { position: absolute; top: 989px; left: 0; width: 692px; height: 211px; background: var(--footer); color: #fff; }
  .footer-brand { position: absolute; left: 37px; top: 22px; font-size: 25px; line-height: 1; color: var(--accent); letter-spacing: 0.5px; }
  .footer-address, .footer-contact { position: absolute; top: 57px; font-size: 12.5px; line-height: 16.5px; font-style: normal; }
  .footer-address { left: 37px; }
  .footer-contact { left: 172px; }
  .footer-career { position: absolute; left: 406px; top: 54px; font-family: "Bebas Neue", sans-serif; font-size: 18px; color: var(--accent); text-decoration: none; line-height: 1; }
  .legal { position: absolute; left: 37px; top: 144px; }
  .legal a { display: block; font-family: "Bebas Neue", sans-serif; font-size: 14px; line-height: 1; color: #fff; text-decoration: none; margin-bottom: 18px; }
</style>
</head>
<body>
  <header class="site-header">
    <div class="brand">kolbrit</div>
    <nav class="main-nav">
      <a href="#">Malerarbeiten</a>
      <a href="#">Betoninstandsetzung</a>
      <a href="#">Balkonabdichtung</a>
      <a href="#">Farbgestaltung</a>
      <a href="#">Waermedaemmung</a>
    </nav>
  </header>

  <section class="hero" role="img" aria-label="Bunte Altbaufassaden in Blau, Orange und Grau vor hellem Himmel">
    <div class="hero-caption">
      <h2>Portrait</h2>
      <p>Lorem ipsum dolor sit amet, consectetuer.</p>
    </div>
  </section>

  <section class="intro">
    <h1>Loremipsum Adipiscing</h1>
    <p>Lorem ipsum dolor sit amet, consectetuer adipiscing elit, sed diam nonummy nibh euismod tincid</p>
    <div class="signature">Mustername Kolbrit</div>
  </section>

  <section class="services">
    <div class="photo photo--square-building" role="img" aria-label="Schwarzweißfoto eines großen Stadtpalais an einer Straßenkreuzung"></div>
    <div class="service-card service-card--concrete">
      <h3>Betoninstandsetzung</h3>
      <p>Lorem ipsum dolor</p>
      <a class="button" href="#">Zur Seite</a>
    </div>
    <div class="photo photo--concrete" role="img" aria-label="Schwarzweißfoto von Händen bei der Betonausbesserung"></div>
    <div class="photo photo--balcony" role="img" aria-label="Beschädigte Balkonkante über einem Rollladen"></div>
    <div class="service-card service-card--soft service-card--balcony">
      <h3>Balkonabdichtung</h3>
      <p>Lorem ipsum dolor</p>
      <a class="button" href="#">Zur Seite</a>
    </div>
    <div class="photo photo--doorway" role="img" aria-label="Schwarzweißfoto eines Altbau-Portals mit Laterne"></div>
    <div class="service-card service-card--insulation">
      <h3>Waermedaemmung</h3>
      <p>Lorem ipsum dolor</p>
      <a class="button" href="#">Zur Seite</a>
    </div>
    <div class="photo photo--facade" role="img" aria-label="Renovierte helle Altbaufassade mit roten Dächern"></div>
  </section>

  <footer class="site-footer">
    <div class="footer-brand">kolbrit</div>
    <address class="footer-address">Kolbrit GmbH<br>Lindenauer Str. 7<br>81999 Falkenau</address>
    <address class="footer-contact">Tel.: +49 89 555 0142<br>Fax: +49 89 555 0143<br>Mail: info@kolbrit-maler.de</address>
    <a class="footer-career" href="#">&gt;&gt;&gt; Ausbildung</a>
    <nav class="legal">
      <a href="#">Impressum</a>
      <a href="#">Datenschutz</a>
    </nav>
  </footer>
</body>
</html>
```